Modern Business Card for Larkwell 2018

Our company assumes the best about people. We are creating an online community of entrepreneurs and business leaders who struggle with marketing their business online.

This business card should POP! We recently got a new logo and are launching a new website next month, so our business cards should make a statement that feels:
-Fresh
-Smart
-Trustworthy
-Fun

Target Market(s)

small business owners, entrepreneurs

Industry/Entity Type

Digital Marketing

Contact Information for Business Card

Dimensions: 3.5" x 2"

Font styles to use
Sans Serif

Colors
f37122
ffffff

Requirements
Must have
• We need a business card with a modern, bold design. We will use one side of the card as a lead-generation offer, so text on one side will need to fit up to 140 characters. The business card should stick to our core colors (orange, black, and white).
Nice to have
• We think a vertical "portrait" design could be interesting.
Should not have
• Should not look like a traditional business card. The round icon should stand out from a distance.

```html
<!DOCTYPE html>
<html lang="en">
<head>
<meta charset="utf-8">
<title>Larkwell Business Card</title>
<link rel="stylesheet" href="https://fonts.googleapis.com/css2?family=Montserrat:wght@800&family=Roboto+Condensed:wght@400;500&display=swap">
<style>
  :root {
    --orange: #f37122;
    --white: #ffffff;
    --card-dark: #353130;
    --card-dark-deep: #2a2725;
    --page: #e4e2e0;
    --muted: #d8d4d1;
  }
  html, body { margin: 0; padding: 0; overflow: hidden; }
  body {
    width: 1200px; height: 896px; background: var(--page);
    display: flex; align-items: center; justify-content: center; gap: 60px;
    font-family: "Roboto Condensed", sans-serif;
  }
  .card {
    position: relative; width: 520px; height: 297px; border-radius: 18px;
    overflow: hidden; color: var(--white);
    background: linear-gradient(135deg, var(--card-dark) 0%, var(--card-dark-deep) 100%);
    box-shadow: 0 10px 26px rgba(0,0,0,.25);
  }
  /* Front: lead-generation side */
  .map-texture {
    position: absolute; inset: 20px 30px 70px 30px; border-radius: 40px;
    background: radial-gradient(ellipse at 45% 50%, rgba(255,255,255,.08), rgba(255,255,255,0) 70%);
  }
  .front-content {
    position: absolute; inset: 0; display: flex; flex-direction: column;
    align-items: center; padding-top: 62px; box-sizing: border-box;
  }
  .brand-row { display: flex; align-items: center; gap: 12px; }
  .brand-dot { width: 38px; height: 38px; border-radius: 50%; background: var(--orange); }
  .brand-name {
    font-family: "Montserrat", sans-serif; font-weight: 800; font-size: 50px;
    letter-spacing: 1px; line-height: 1; color: var(--white);
  }
  .offer {
    margin: 14px 0 0; font-size: 13px; text-align: center; line-height: 1.35; color: var(--muted);
  }
  .tagline {
    position: absolute; left: 0; right: 0; bottom: 44px; margin: 0; text-align: center;
    font-size: 14px; font-weight: 400; letter-spacing: .3px; line-height: 1;
  }
  .tagline-rule {
    position: absolute; left: 40px; right: 40px; bottom: 32px; height: 2px; background: var(--orange);
  }
  /* Back: contact side */
  .back-art { position: absolute; inset: 0; }
  .contact {
    position: absolute; left: 34px; top: 40px;
  }
  .contact .brand-name { font-size: 34px; }
  .person { margin-top: 18px; font-size: 21px; font-weight: 500; letter-spacing: .5px; line-height: 1; }
  .role { font-size: 14px; color: var(--muted); margin-top: 3px; }
  .address { margin-top: 14px; font-size: 13px; line-height: 1.35; color: var(--muted); }
  .lines { list-style: none; margin: 12px 0 0; padding: 0; font-size: 13px; line-height: 1.5; }
  .lines li { display: flex; align-items: center; gap: 7px; }
  .lines svg { width: 11px; height: 11px; fill: var(--white); flex: none; }
</style>
</head>
<body>

<section class="card card-front" aria-label="Card front: offer">
  <div class="map-texture" role="img" aria-label="Faint dotted world map texture"></div>
  <div class="front-content">
    <div class="brand-row">
      <span class="brand-dot"></span>
      <span class="brand-name">LARKWELL</span>
    </div>
    <p class="offer">Get your free Larkwell<br>Starter Package and our marketing guide today at</p>
  </div>
  <p class="tagline">REACH MORE PEOPLE. MAKE MORE MONEY. CREATE MORE IMPACT.</p>
  <div class="tagline-rule"></div>
</section>

<section class="card card-back" aria-label="Card back: contact">
  <svg class="back-art" viewBox="0 0 520 297" aria-hidden="true">
    <path d="M300 0 H520 V297 H340 C250 250 225 120 300 0 Z" fill="var(--white)"/>
    <circle cx="400" cy="130" r="100" fill="var(--orange)"/>
  </svg>
  <div class="contact">
    <div class="brand-name">LARKWELL</div>
    <div class="person">MILES CORBIN</div>
    <div class="role">Story Marketing Coach</div>
    <div class="address">RV2040, 8/3 Linden Row<br>Harbor city, Westmark</div>
    <ul class="lines">
      <li><svg viewBox="0 0 24 24"><path d="M6.6 10.8a15 15 0 0 0 6.6 6.6l2.2-2.2a1 1 0 0 1 1-.25 11.4 11.4 0 0 0 3.6.57 1 1 0 0 1 1 1V20a1 1 0 0 1-1 1A17 17 0 0 1 3 4a1 1 0 0 1 1-1h3.5a1 1 0 0 1 1 1c0 1.25.2 2.45.57 3.6a1 1 0 0 1-.25 1z"/></svg>(555) 014-2280</li>
      <li><svg viewBox="0 0 24 24"><path d="M2 5h20v14H2z M4 7v1l8 5 8-5V7l-8 5z" fill-rule="evenodd"/></svg>miles@larkwellnow.com</li>
      <li><svg viewBox="0 0 24 24"><circle cx="12" cy="12" r="10"/></svg>www.larkwellnow.com</li>
    </ul>
  </div>
</section>

</body>
</html>
```